BOLD & MINIMALIST DESIGN NEEDED

We want a very bold but minimalistic business card design that is impactful and utilizes both sides of the business card. Our current logo is included for your use.

We want bold fonts and good use of negative space. We don't want the logo to overpower the design.

Target Market(s)

Professionals who are building new commercial buildings.

Industry/Entity Type

Construction

Contact Information for Business Card

Name, Title, email, office phone, cell phone, website

Font styles to use
Serif
Sans Serif

Requirements
Must have
• Bold design!

```html
<!DOCTYPE html>
<html lang="en">
<head>
<meta charset="utf-8">
<title>Ridgeline Build Co — Business Card</title>
<link href="https://fonts.googleapis.com/css2?family=Poppins:wght@400;500;600;700;800&display=swap" rel="stylesheet">
<style>
  :root {
    --bg: #2a2a2a;
    --card-dark: #111111;
    --card-light: #ffffff;
    --green: #7dc242;
    --ink: #111111;
    --ink-soft: #2b2b2b;
    --white: #ffffff;
  }
  * { box-sizing: border-box; margin: 0; padding: 0; }
  html, body {
    width: 1200px; height: 875px; overflow: hidden;
    background: var(--bg);
    font-family: "Poppins", sans-serif;
  }
  .stage { position: relative; width: 1200px; height: 875px; }
  .card {
    position: absolute; top: 283px;
    width: 540px; height: 309px;
    border-radius: 14px; overflow: hidden;
  }
  /* Back side */
  .card--back { left: 40px; background: var(--card-dark); }
  .card--back .brand {
    position: absolute; inset: 0;
    display: flex; align-items: center; justify-content: center; gap: 14px;
  }
  .brand__mark { width: 22px; height: 22px; background: var(--green); }
  .brand__name {
    font-weight: 800; font-size: 36px; letter-spacing: 0.5px;
    color: var(--white); text-transform: uppercase;
  }
  /* Front side */
  .card--front { left: 620px; background: var(--card-light); }
  .card--front .brand {
    position: absolute; left: 38px; top: 62px;
    display: flex; align-items: center; gap: 10px;
  }
  .card--front .brand__mark { width: 16px; height: 16px; }
  .card--front .brand__name { font-size: 26px; color: var(--ink); }
  .person { position: absolute; left: 38px; top: 150px; }
  .person__name { font-weight: 600; font-size: 24px; color: var(--green); line-height: 1.1; }
  .person__title { font-size: 12px; color: var(--ink-soft); }
  .rule {
    position: absolute; left: 38px; right: 28px; top: 205px;
    height: 1.5px; background: var(--green);
  }
  .contacts {
    position: absolute; left: 38px; top: 214px;
    list-style: none; font-size: 12px; color: var(--ink); line-height: 20px;
  }
  .contacts li { display: flex; align-items: center; gap: 8px; }
  .contacts svg { width: 10px; height: 10px; fill: var(--green); flex: none; }
  .address {
    position: absolute; right: 28px; top: 232px;
    text-align: right; font-size: 12px; color: var(--ink); line-height: 17px;
  }
  .band {
    position: absolute; right: 0; bottom: 0;
    width: 175px; height: 12px; background: var(--green);
  }
</style>
</head>
<body>
<main class="stage">
  <section class="card card--back" aria-label="Card back">
    <div class="brand">
      <span class="brand__mark"></span>
      <span class="brand__name">Ridgeline Build Co</span>
    </div>
  </section>

  <section class="card card--front" aria-label="Card front">
    <div class="brand">
      <span class="brand__mark"></span>
      <span class="brand__name">Ridgeline Build Co</span>
    </div>
    <div class="person">
      <p class="person__name">Jordan Hale</p>
      <p class="person__title">Head contractor</p>
    </div>
    <div class="rule"></div>
    <ul class="contacts">
      <li><svg viewBox="0 0 10 10"><path d="M1 2.5 Q1 1 2.5 1 L3.5 1 4 3 3 3.8 Q4 6 6.2 7 L7 6 9 6.5 9 7.5 Q9 9 7.5 9 Q1 8.5 1 2.5Z"/></svg>555.301.2200</li>
      <li><svg viewBox="0 0 10 10"><path d="M2.5 0.5 H7.5 V9.5 H2.5Z M3.3 1.5 V7.8 H6.7 V1.5Z"/></svg>555-301-2201</li>
      <li><svg viewBox="0 0 10 10"><path d="M0.5 2 H9.5 V8 H0.5Z M1.2 2.6 5 5.4 8.8 2.6"/></svg>info@ridgeline-bc.com</li>
      <li><svg viewBox="0 0 10 10"><circle cx="5" cy="5" r="4.5"/></svg>www.ridgeline-bc.com</li>
    </ul>
    <p class="address">1420 Cedar Hollow Rd.<br>Fairmont Ridge, GA 30999</p>
    <div class="band"></div>
  </section>
</main>
</body>
</html>
```